Business Card Design for Marketing Firm

Looking for business card design for higher end marketing firm. Clean but impressionable/trendy. We are a marketing firm that represents manufacturers in the foodservice equipment and supply industry. Our customers are end users such has hotels, restaurants, country clubs, convention centers and casinos as well as distributors of restaurants supplies and equipment, and manufacturers of foodservice equipment and supplies.
Target Market(s)
Hotels, Restaurants, Supply & Equipment Distributors, Foodservice Manufacturers
Industry/Entity Type
Foodservice/Hospitality
Contact Information for Business Card
Name, Title, Contact Number, Email, Website, Social Media, Address
Requirements
Must have
- Clean & Simple but Serious and Impressionable

```html
<!DOCTYPE html>
<html lang="en">
<head>
<meta charset="utf-8">
<title>Meridian Partners – Business Card</title>
<link href="https://fonts.googleapis.com/css2?family=Montserrat:wght@500;800&display=swap" rel="stylesheet">
<style>
  :root {
    --brand-blue: #2b2a7e;
    --brand-blue-light: #363592;
    --paper: #ffffff;
    --ink: #1b1b2b;
    --backdrop: #3a3a3c;
  }
  * { margin: 0; padding: 0; box-sizing: border-box; }
  html, body { width: 1200px; height: 960px; overflow: hidden; }
  body {
    background: var(--backdrop);
    font-family: "Montserrat", sans-serif;
    position: relative;
  }
  .card {
    position: absolute;
    width: 620px;
    height: 354px;
    border-radius: 22px;
    overflow: hidden;
  }
  .card--front {
    left: 80px; top: 80px;
    background: linear-gradient(135deg, var(--brand-blue-light), var(--brand-blue));
  }
  .card--back {
    left: 500px; top: 506px;
    background: var(--paper);
  }
  .wordmark {
    position: absolute;
    font-family: "Montserrat", sans-serif;
    font-weight: 500;
    letter-spacing: 2px;
    line-height: 1.3;
    display: flex;
    align-items: center;
    gap: 12px;
    white-space: nowrap;
  }
  .wordmark__dot { border-radius: 50%; flex: none; }
  .card--front .wordmark {
    color: var(--paper);
    left: 0; right: 0; top: 158px;
    justify-content: center;
    font-size: 30px;
  }
  .card--front .wordmark__dot { background: var(--paper); width: 16px; height: 16px; }
  .card--back .wordmark {
    color: var(--brand-blue);
    left: 20px; top: 168px;
    width: 260px;
    justify-content: center;
    font-size: 17px;
    letter-spacing: 1.2px;
  }
  .card--back .wordmark__dot { background: var(--brand-blue); width: 11px; height: 11px; }
  .back-bands { position: absolute; inset: 0; }
  .divider {
    position: absolute;
    left: 292px; top: 56px;
    width: 1.5px; height: 200px;
    background: var(--brand-blue);
  }
  .contact {
    position: absolute;
    left: 314px; top: 46px;
    color: var(--ink);
    font-size: 13px;
    font-weight: 500;
    line-height: 1.45;
  }
  .contact__name {
    color: var(--brand-blue);
    font-weight: 800;
    font-size: 20px;
    letter-spacing: 0.2px;
  }
  .contact__title { margin-bottom: 8px; }
  .contact__address { margin-bottom: 8px; }
  .contact__row { display: flex; align-items: center; gap: 8px; }
  .contact__row svg { width: 14px; height: 14px; flex: none; }
  .social { display: flex; align-items: center; gap: 5px; margin-top: 4px; }
  .social__dot { width: 14px; height: 14px; border-radius: 50%; background: var(--brand-blue); }
  .social__handle { margin-left: 4px; }
</style>
</head>
<body>

  <section class="card card--front" aria-label="Card front">
    <div class="wordmark">
      <span class="wordmark__dot"></span>
      <span>MERIDIAN PARTNERS</span>
    </div>
  </section>

  <section class="card card--back" aria-label="Card back">
    <svg class="back-bands" viewBox="0 0 620 354" preserveAspectRatio="none">
      <polygon points="0,326 620,326 620,354 0,354" fill="var(--brand-blue)"/>
      <polygon points="428,268 620,268 620,354 408,354" fill="var(--brand-blue)"/>
      <polygon points="418,268 426,268 406,354 398,354" fill="var(--paper)"/>
    </svg>

    <div class="wordmark">
      <span class="wordmark__dot"></span>
      <span>MERIDIAN PARTNERS</span>
    </div>

    <div class="divider"></div>

    <div class="contact">
      <div class="contact__name">DANIEL MORROW</div>
      <div class="contact__title">Co-Founder</div>
      <div class="contact__address">P.O. BOX 40-12 LNS-22<br>Linden Ave 14, Fairview</div>
      <div class="contact__row">
        <svg viewBox="0 0 16 16"><path d="M4 1.5l2.5 3-1.4 1.6c.8 1.8 2.1 3.1 3.9 3.9l1.6-1.4 3 2.5-1.6 2.4C7.5 13.6 2.4 8.5 1.6 3.1z" fill="var(--brand-blue)"/></svg>
        <span>555-014-2290</span>
      </div>
      <div class="contact__row">
        <svg viewBox="0 0 16 16"><rect x="1" y="3" width="14" height="10" fill="var(--brand-blue)"/><path d="M1 3l7 5.5L15 3" stroke="#fff" stroke-width="1.3" fill="none"/></svg>
        <span>info@meridianpartners.com</span>
      </div>
      <div class="contact__row">
        <svg viewBox="0 0 16 16"><circle cx="8" cy="8" r="6.5" fill="none" stroke="var(--brand-blue)" stroke-width="1.6"/><path d="M1.5 8h13M8 1.5c-3 3.5-3 9.5 0 13M8 1.5c3 3.5 3 9.5 0 13" stroke="var(--brand-blue)" stroke-width="1.2" fill="none"/></svg>
        <span>www.meridianpartners.com</span>
      </div>
      <div class="social">
        <span class="social__dot"></span>
        <span class="social__dot"></span>
        <span class="social__dot"></span>
        <span class="social__dot"></span>
        <span class="social__handle">@meridianpartners</span>
      </div>
    </div>
  </section>

</body>
</html>
```